Kestrel Facilities Business Card Design

We would now like to design business cards with the new Kestrel Facilities logo

Target Market(s)

Professional

Industry/Entity Type

Professional services

Contact Information for Business Card

Employee name, title, phone number, email address, corporate office address and logo.

Font styles to use
Sans Serif

Colors
0054AA
0677BA
7BADD7
CADEEF
E8F1F8

Requirements
Must have
• My logo
Should not have
• any other pictures or images besides my logo

```html
<!DOCTYPE html>
<html lang="en">
<head>
<meta charset="utf-8">
<title>Kestrel Facilities Business Card</title>
<link href="https://fonts.googleapis.com/css2?family=Montserrat:wght@400;500;700&display=swap" rel="stylesheet">
<style>
  :root {
    --brand-blue: #3578bf;
    --band-grey: #a7a8ab;
    --card-white: #ffffff;
    --backdrop: #d9dadc;
    --text-light: #ffffff;
  }
  * { margin: 0; padding: 0; box-sizing: border-box; }
  html, body {
    width: 1200px;
    height: 900px;
    overflow: hidden;
    background: var(--backdrop);
    font-family: "Montserrat", sans-serif;
  }
  .canvas { position: relative; width: 1200px; height: 900px; }
  .card {
    position: absolute;
    width: 560px;
    height: 320px;
    border-radius: 22px;
    background: var(--card-white);
    overflow: hidden;
    box-shadow: 0 6px 18px rgba(0,0,0,0.18);
  }
  .card--back { left: 50px; top: 80px; }
  .card--front { left: 590px; top: 500px; }

  .brand {
    display: flex;
    align-items: center;
    gap: 10px;
    color: var(--brand-blue);
    font-weight: 700;
    text-transform: uppercase;
    letter-spacing: 0.04em;
    line-height: 1;
  }
  .brand__square { background: var(--brand-blue); flex: none; }

  .card--back .brand {
    position: absolute;
    left: 50%; top: 50%;
    transform: translate(-50%, -50%);
    font-size: 30px;
    white-space: nowrap;
  }
  .card--back .brand__square { width: 26px; height: 26px; }

  .card--front .brand {
    position: absolute;
    right: 34px; top: 34px;
    font-size: 19px;
    white-space: nowrap;
  }
  .card--front .brand__square { width: 17px; height: 17px; }

  .wave { position: absolute; left: 0; top: 0; width: 560px; height: 320px; }

  .contact {
    position: absolute;
    left: 40px; top: 168px;
    color: var(--text-light);
  }
  .contact__name { font-size: 20px; font-weight: 700; letter-spacing: 0.02em; }
  .contact__title { font-size: 13px; font-weight: 400; margin-top: 2px; }
  .contact__address { font-size: 12.5px; line-height: 1.35; margin-top: 12px; }
  .contact__lines { margin-top: 10px; font-size: 12.5px; }
  .contact__line { display: flex; align-items: center; gap: 8px; line-height: 1.55; }
  .contact__icon { width: 13px; height: 13px; flex: none; }
</style>
</head>
<body>
<main class="canvas">

  <section class="card card--back" aria-label="Business card back">
    <div class="brand"><span class="brand__square"></span><span>Kestrel Facilities</span></div>
  </section>

  <section class="card card--front" aria-label="Business card front">
    <svg class="wave" viewBox="0 0 560 320" aria-hidden="true">
      <path fill="var(--band-grey)" d="M0,136 C140,106 260,96 380,96 C470,96 520,81 560,41 L560,320 L0,320 Z"/>
      <path fill="var(--card-white)" d="M0,145 C140,115 260,105 380,105 C470,105 520,90 560,50 L560,320 L0,320 Z"/>
      <path fill="var(--brand-blue)" d="M0,150 C140,120 260,110 380,110 C470,110 520,95 560,55 L560,320 L0,320 Z"/>
    </svg>

    <div class="brand"><span class="brand__square"></span><span>Kestrel Facilities</span></div>

    <div class="contact">
      <p class="contact__name">DARA WHITCOMBE</p>
      <p class="contact__title">Co-Founder</p>
      <p class="contact__address">1480 N. Harbor Lane<br>Suite 210 Larkfield 42</p>
      <div class="contact__lines">
        <p class="contact__line">
          <svg class="contact__icon" viewBox="0 0 24 24" aria-hidden="true"><path fill="#fff" d="M6.6 10.8a15.1 15.1 0 0 0 6.6 6.6l2.2-2.2a1 1 0 0 1 1-.25 11.4 11.4 0 0 0 3.6.57 1 1 0 0 1 1 1V20a1 1 0 0 1-1 1A17 17 0 0 1 3 4a1 1 0 0 1 1-1h3.5a1 1 0 0 1 1 1c0 1.25.2 2.45.57 3.57a1 1 0 0 1-.25 1z"/></svg>
          <span>+254-732-41057</span>
        </p>
        <p class="contact__line">
          <svg class="contact__icon" viewBox="0 0 24 24" aria-hidden="true"><path fill="#fff" d="M3 5h18a1 1 0 0 1 1 1v12a1 1 0 0 1-1 1H3a1 1 0 0 1-1-1V6a1 1 0 0 1 1-1zm9 7.2L4.2 7h15.6zM4 8.6V17h16V8.6l-8 5.3z"/></svg>
          <span>hello@kestrelfacilities.com</span>
        </p>
      </div>
    </div>
  </section>

</main>
</body>
</html>
```